Wellpath Ledgers New Website

Please review the attached Design Brief with additional details. Thank you!

The goal is to create a website that effectively communicates the benefits of WellPath Ledgers to eye care professionals. The website should streamline the process of understanding and utilizing WellPath Ledgers' services, emphasizing improved patient outcomes, increased referrals, and enhanced patient engagement.

Target Market(s)

Eyecare Professionals

Number of Pages Required

4 page

```html
<!DOCTYPE html>
<html lang="en">
<head>
<meta charset="utf-8">
<title>Wellpath Ledgers</title>
<link rel="stylesheet" href="https://fonts.googleapis.com/css2?family=Open+Sans:wght@300;400;600;700&family=Tinos:wght@400;700&display=swap">
<style>
:root{
  --navy:#13295c;
  --blue:#1b5bab;
  --orange:#f9a63a;
  --lav:#efecf5;
  --lav-deep:#e4dff0;
  --dark:#262b36;
  --darker:#1b2238;
  --text:#5d6170;
  --white:#fff;
}
*{box-sizing:border-box;margin:0;padding:0}
html,body{width:1200px;height:4521px;overflow:hidden}
body{position:relative;background:var(--white);font-family:"Open Sans",sans-serif;color:var(--text)}
.abs{position:absolute}
.serif{font-family:"Tinos",serif}
.brand{font-family:"Open Sans",sans-serif;font-weight:600;color:var(--navy);display:flex;align-items:center;gap:10px}
.brand .dot{width:16px;height:16px;border-radius:50%;background:var(--orange)}

/* header */
.site-header{top:0;left:0;width:1200px;height:123px;background:var(--white);z-index:3}
.contact-mini{top:18px;display:flex;gap:12px;align-items:center;font-size:10px;color:#777}
.contact-mini b{display:block;color:var(--navy);font-size:11px}
.contact-mini .ic{width:30px;height:30px;border-radius:50%;background:var(--navy);display:flex;align-items:center;justify-content:center}
.book-btn{left:879px;top:14px;width:184px;height:37px;border-radius:19px;background:var(--navy);color:#fff;font-size:11px;font-weight:700;display:flex;align-items:center;justify-content:center;letter-spacing:.3px}
.nav a{position:absolute;top:87px;font-size:11px;color:#666;text-decoration:none}
.logo-tab{left:495px;top:0;width:200px;height:146px;background:#fff;border-radius:0 0 30px 30px;display:flex;align-items:center;justify-content:center;z-index:4}
.logo-tab .brand{font-size:22px}

/* hero */
.hero{top:123px;left:0;width:1200px;height:780px;background:linear-gradient(100deg,#2f3540 0%,#4c5563 40%,#6b7584 70%,#4a5260 100%)}
.hero-kicker{left:82px;top:366px;color:#fff;font-size:17px;font-weight:700;letter-spacing:6px}
.hero h1{left:76px;top:412px;color:#fff;font-size:44px;font-weight:600;letter-spacing:.5px}
.hero-rule{left:78px;top:494px;width:702px;height:2px;background:rgba(255,255,255,.7)}
.hero p{left:82px;top:524px;width:640px;color:#fff;font-size:15px;line-height:28px}
.btn{display:flex;align-items:center;justify-content:center;border-radius:20px;font-size:12px;font-weight:700}
.btn-orange{background:var(--orange);color:#fff}
.btn-white{background:#fff;color:var(--navy)}

/* about */
.about-photo{left:92px;top:958px;width:462px;height:462px;border-radius:50%;border:7px solid var(--blue);border-left-color:transparent;border-bottom-color:transparent;transform:rotate(10deg)}
.about-photo-fill{left:96px;top:970px;width:444px;height:444px;border-radius:50%;background:linear-gradient(140deg,#c9d3db,#7fa6c2 55%,#4c7ea6)}
.kicker-orange{color:var(--orange);font-family:"Tinos",serif;font-size:15px}
.about h2{font-family:"Tinos",serif;font-weight:400;color:var(--navy);font-size:35px}
.quote-box{left:621px;top:1080px;width:460px;padding-left:14px;border-left:3px solid var(--navy);font-size:13px;line-height:23px}
.body-copy{font-size:13px;line-height:23.5px}

/* services */
.services{top:1513px;left:0;width:1200px;height:572px;background:var(--lav)}
.section-title{width:1200px;text-align:center;font-family:"Tinos",serif;color:var(--navy);font-size:45px}
.section-sub{width:1200px;text-align:center;font-size:13px;line-height:23px}
.svc-card{top:1750px;width:320px;height:268px;border-radius:4px;overflow:hidden}
.svc-card .shade{position:absolute;inset:0;background:linear-gradient(rgba(20,24,35,.55),rgba(20,24,35,.35))}
.svc-card h3{position:absolute;left:20px;top:66px;color:#fff;font-family:"Tinos",serif;font-size:30px;font-weight:700}
.svc-card svg.arrow{position:absolute;left:42px;top:208px}
.svc-icon{width:72px;height:72px;border-radius:50%;background:#fff;top:1714px;display:flex;align-items:center;justify-content:center;box-shadow:0 4px 10px rgba(0,0,0,.08);z-index:2}

/* why */
.why-wing{top:2317px;height:430px;background:linear-gradient(90deg,rgba(239,236,245,0),var(--lav-deep))}
.why-wing.right{background:linear-gradient(270deg,rgba(239,236,245,0),var(--lav-deep))}
.why-photo{left:432px;top:2300px;width:330px;height:400px;border-radius:165px 165px 165px 165px;background:linear-gradient(180deg,#d9dbe0,#8a8f99 60%,#5f646d)}
.why-item h4{font-family:"Tinos",serif;font-weight:400;font-size:22px;color:var(--navy)}
.why-item p{font-size:13px;line-height:23px;margin-top:6px}
.why-icon{width:88px;height:88px;border-radius:50%;background:var(--navy);border:5px solid #f2e6d6;display:flex;align-items:center;justify-content:center;box-shadow:0 0 0 5px #fff}

/* appointment */
.appt{top:2817px;left:0;width:1200px;height:561px;background:linear-gradient(100deg,#2a2f39,#3d4350 50%,#545b68)}
.hours-title{left:95px;top:2945px;color:#fff;font-family:"Tinos",serif;font-size:29px}
.hours-table{left:97px;top:3012px;width:456px;height:236px;background:rgba(255,255,255,.06);border-left:4px solid var(--orange)}
.hours-row{position:absolute;left:36px;right:0;display:flex;justify-content:space-between;color:#fff;font-size:14px}
.hours-row b{font-weight:600}
.hours-row span{color:#d6d8de}
.appt-panel{left:610px;top:2843px;width:492px;height:497px;background:var(--lav-deep)}
.field{position:absolute;background:#fff;font-size:13px;color:#444;display:flex;align-items:center;padding-left:27px;height:52px}

/* reviews */
.review{top:3650px;width:320px;height:267px;background:#fff;box-shadow:0 4px 20px rgba(40,40,80,.08)}
.review .avatar{position:absolute;left:34px;top:-24px;width:60px;height:60px;border-radius:50%;background:linear-gradient(#d9c7b8,#8c7a6d);border:3px solid #fff}
.review .qmark{position:absolute;right:30px;top:-42px;font-family:"Tinos",serif;font-size:110px;color:#5aa8e8;line-height:1}
.review .stars{position:absolute;left:28px;top:62px;color:var(--orange);font-size:15px;letter-spacing:4px}
.review p{position:absolute;left:28px;top:88px;width:270px;font-size:12.5px;line-height:23.5px}
.review h5{position:absolute;left:28px;top:188px;font-family:"Tinos",serif;font-weight:400;font-size:20px;color:#333}
.review small{position:absolute;left:28px;top:218px;font-size:10px;color:var(--blue)}

/* footer */
.site-footer{top:3984px;left:0;width:1200px;height:482px;background:var(--dark)}
.foot-nav a{position:absolute;top:4283px;color:#fff;font-size:14px;text-decoration:none}
.foot-contact{position:absolute;top:4378px;display:flex;align-items:center;gap:14px;color:#fff;font-size:12px;line-height:18px}
.foot-contact .ring{width:56px;height:56px;border-radius:50%;border:1.5px solid rgba(255,255,255,.7);display:flex;align-items:center;justify-content:center}
.bottom-bar{top:4466px;left:0;width:1200px;height:55px;background:var(--darker)}
.social{width:24px;height:24px;border:1px solid #fff;top:4482px}
</style>
</head>
<body>

<!-- header -->
<header class="abs site-header">
  <div class="abs contact-mini" style="left:124px">
    <div class="ic"><svg width="14" height="14" viewBox="0 0 24 24" fill="#fff"><path d="M6.6 10.8a15 15 0 0 0 6.6 6.6l2.2-2.2c.3-.3.7-.4 1-.2 1.1.4 2.3.6 3.6.6.6 0 1 .4 1 1V20c0 .6-.4 1-1 1A17 17 0 0 1 3 4c0-.6.4-1 1-1h3.5c.6 0 1 .4 1 1 0 1.3.2 2.5.6 3.6.1.3 0 .7-.2 1z"/></svg></div>
    <div><b>Call Us:</b>(555) 014 2238</div>
  </div>
  <div class="abs contact-mini" style="left:281px">
    <div class="ic"><svg width="14" height="14" viewBox="0 0 24 24" fill="none" stroke="#fff" stroke-width="2"><rect x="3" y="5" width="18" height="14" rx="2"/><path d="M3 7l9 6 9-6"/></svg></div>
    <div><b>Email:</b>office@wellpathledgers.com</div>
  </div>
  <a class="abs book-btn">BOOK APPOINTMENT</a>
  <nav class="nav">
    <a style="left:125px">Home</a>
    <a style="left:237px">About Us</a>
    <a style="left:386px">Services</a>
    <a style="left:707px">Team</a>
    <a style="left:833px">Blog</a>
    <a style="left:958px">Contact Us</a>
  </nav>
</header>
<div class="abs logo-tab"><div class="brand"><span class="dot"></span>Wellpath Ledgers</div></div>

<!-- hero -->
<section class="abs hero" role="img" aria-label="Team of professionals working at computers in a bright open-plan office"></section>
<svg class="abs" style="left:0;top:770px" width="1200" height="150" viewBox="0 0 1200 150">
  <path d="M0 20 Q600 160 1200 20 L1200 150 L0 150 Z" fill="#fff"/>
  <path d="M240 92 Q600 145 960 92" fill="none" stroke="var(--orange)" stroke-width="3"/>
  <circle cx="600" cy="122" r="27" fill="#fff" stroke="#eee" stroke-width="2"/>
  <circle cx="600" cy="122" r="7" fill="var(--orange)"/>
</svg>
<div class="abs hero-kicker">WELLPATH LEDGERS</div>
<h1 class="abs" style="left:76px;top:412px;color:#fff;font-size:44px;font-weight:600">Insightful Data, Better Outcomes</h1>
<div class="abs hero-rule"></div>
<p class="abs" style="left:82px;top:524px;width:640px;color:#fff;font-size:15px;line-height:28px">Lorem ipsum dolor sit amet, consectetur adipiscing elit, sed do eiusmod tempor incididunt ut labore et dolore magna</p>
<a class="abs btn btn-orange" style="left:82px;top:612px;width:146px;height:38px">LEARN MORE</a>
<a class="abs btn btn-white" style="left:240px;top:612px;width:180px;height:38px">REQUEST QUOTE</a>

<!-- about -->
<section class="about">
  <div class="abs about-photo-fill" role="img" aria-label="Nurse in blue scrubs reviewing records on a tablet"></div>
  <div class="abs about-photo"></div>
  <div class="abs kicker-orange" style="left:621px;top:976px">Empowering Eye Care Excellence</div>
  <h2 class="abs" style="left:621px;top:1013px">Brighter Vision, Sharper Records</h2>
  <div class="abs quote-box">Lorem ipsum dolor sit amet, consectetur adipiscing elit, sed do eiusmod or incididunt ut labore et dolore</div>
  <p class="abs body-copy" style="left:621px;top:1160px;width:470px">Lorem ipsum dolor sit amet, consectetur adipiscing elit, sed do eiusmod obgr incididunt ut labore et dolore Lorem ipsum dolor sit amet, consectetur adip iscing elit, sed do eiusmod tempor incididunt ut labore et dolore m agna aliqua. Ut enim ad minim veniam, quis nostrud exercitation ullamco laboris nisi ut aliquip ex ea commodo consequat.</p>
  <p class="abs body-copy" style="left:621px;top:1293px;width:470px">Lorem ipsum dolor sit amet, consectetur adipiscing elit, sed do eiusmod obgr incididunt ut labore et dolore Lorem ipsum dol</p>
  <a class="abs btn btn-orange" style="left:620px;top:1360px;width:138px;height:44px;border-radius:0 20px 20px 0;font-size:14px;font-weight:600">Contact us</a>
</section>

<!-- services -->
<section class="abs services"></section>
<h2 class="abs section-title" style="left:0;top:1562px;font-weight:400">Our Services</h2>
<p class="abs section-sub" style="left:0;top:1628px">Lorem ipsum dolor sit amet, consectetur adipiscing elit, sed do eiusmod temp<br>or incididunt ut labore et dolore</p>

<div class="abs svc-icon" style="left:134px"><svg width="32" height="32" viewBox="0 0 24 24" fill="none" stroke="var(--orange)" stroke-width="1.5"><circle cx="12" cy="12" r="8"/><circle cx="12" cy="12" r="3"/></svg></div>
<div class="abs svc-icon" style="left:483px"><svg width="32" height="32" viewBox="0 0 24 24" fill="none" stroke="var(--orange)" stroke-width="1.5"><circle cx="12" cy="12" r="6"/><path d="M12 2v4M12 18v4M2 12h4M18 12h4"/></svg></div>
<div class="abs svc-icon" style="left:831px"><svg width="32" height="32" viewBox="0 0 24 24" fill="none" stroke="var(--orange)" stroke-width="1.5"><circle cx="12" cy="8" r="3"/><path d="M5 20c1-4 4-6 7-6s6 2 7 6z"/></svg></div>

<article class="abs svc-card" style="left:91px" role="img" aria-label="Doctors reviewing paperwork at a desk">
  <div style="position:absolute;inset:0;background:linear-gradient(135deg,#b8b2a8,#6f6a66)"></div><div class="shade"></div>
  <h3>Data Management</h3>
  <svg class="arrow" width="46" height="20" viewBox="0 0 46 20" fill="none" stroke="#fff" stroke-width="2"><path d="M0 10h44M34 1l10 9-10 9"/></svg>
</article>
<article class="abs svc-card" style="left:439px" role="img" aria-label="Analyst monitoring charts across several screens">
  <div style="position:absolute;inset:0;background:linear-gradient(135deg,#c8ccd2,#6c737d)"></div><div class="shade"></div>
  <h3>Outcome Monitoring</h3>
  <svg class="arrow" width="46" height="20" viewBox="0 0 46 20" fill="none" stroke="#fff" stroke-width="2"><path d="M0 10h44M34 1l10 9-10 9"/></svg>
</article>
<article class="abs svc-card" style="left:786px" role="img" aria-label="Clinician discussing a document with a patient">
  <div style="position:absolute;inset:0;background:linear-gradient(135deg,#a9b8c8,#5e6f82)"></div><div class="shade"></div>
  <h3>Engagement Tools</h3>
  <svg class="arrow" width="46" height="20" viewBox="0 0 46 20" fill="none" stroke="#fff" stroke-width="2"><path d="M0 10h44M34 1l10 9-10 9"/></svg>
</article>

<!-- why choose -->
<h2 class="abs section-title" style="left:0;top:2138px;font-weight:400">Why Choose Us</h2>
<p class="abs section-sub" style="left:0;top:2204px">Lorem ipsum dolor sit amet, consectetur adipiscing elit, sed do eiusmod temp<br>or incididunt ut labore et dolore</p>
<div class="abs why-wing" style="left:140px;width:400px;border-radius:0 215px 215px 0"></div>
<div class="abs why-wing right" style="left:660px;width:400px;border-radius:215px 0 0 215px"></div>
<div class="abs why-photo" role="img" aria-label="Smiling businessman in a grey suit with arms crossed"></div>

<div class="abs why-item" style="left:130px;top:2358px;width:248px;text-align:right"><h4>Quality Assurance</h4><p>Lorem ipsum dolor sit amet, conser adi or incididunt ut labore et dolore</p></div>
<div class="abs why-item" style="left:130px;top:2489px;width:248px;text-align:right"><h4>Client-Centric</h4><p>Lorem ipsum dolor sit amet, conser adi or incididunt ut labore et dolore</p></div>
<div class="abs why-item" style="left:130px;top:2623px;width:248px;text-align:right"><h4>Personalized Approach</h4><p>Lorem ipsum dolor sit amet, conser adi or incididunt ut labore et dolore</p></div>
<div class="abs why-item" style="left:799px;top:2358px;width:260px"><h4>Proven Track Record</h4><p>Lorem ipsum dolor sit amet, conser adi or incididunt ut labore et dolore</p></div>
<div class="abs why-item" style="left:799px;top:2489px;width:260px"><h4>Quality Assurance</h4><p>Lorem ipsum dolor sit amet, conser adi or incididunt ut labore et dolore</p></div>
<div class="abs why-item" style="left:799px;top:2623px;width:260px"><h4>Specialized Workshops</h4><p>Lorem ipsum dolor sit amet, conser adi or incididunt ut labore et dolore</p></div>

<div class="abs why-icon" style="left:398px;top:2360px"><svg width="34" height="34" viewBox="0 0 24 24" fill="none" stroke="#fff" stroke-width="1.5"><path d="M4 16a8 8 0 1 1 16 0"/><path d="M12 16l3-5"/></svg></div>
<div class="abs why-icon" style="left:398px;top:2492px"><svg width="34" height="34" viewBox="0 0 24 24" fill="none" stroke="#fff" stroke-width="1.5"><circle cx="12" cy="12" r="3"/><circle cx="12" cy="12" r="8" stroke-dasharray="3 2"/></svg></div>
<div class="abs why-icon" style="left:398px;top:2624px"><svg width="34" height="34" viewBox="0 0 24 24" fill="none" stroke="#fff" stroke-width="1.5"><circle cx="12" cy="8" r="3"/><path d="M5 20c1-4 4-6 7-6s6 2 7 6z"/></svg></div>
<div class="abs why-icon" style="left:691px;top:2360px"><svg width="34" height="34" viewBox="0 0 24 24" fill="none" stroke="#fff" stroke-width="1.5"><path d="M12 3l2.7 5.6 6.1.9-4.4 4.3 1 6.1L12 17l-5.4 2.9 1-6.1-4.4-4.3 6.1-.9z"/></svg></div>
<div class="abs why-icon" style="left:691px;top:2492px"><svg width="34" height="34" viewBox="0 0 24 24" fill="none" stroke="#fff" stroke-width="1.5"><path d="M20 12a8 8 0 0 1-14 5M4 12a8 8 0 0 1 14-5"/><path d="M18 3v4h-4M6 21v-4h4"/></svg></div>
<div class="abs why-icon" style="left:691px;top:2624px"><svg width="34" height="34" viewBox="0 0 24 24" fill="none" stroke="#fff" stroke-width="1.5"><circle cx="8" cy="8" r="3"/><circle cx="16" cy="8" r="3"/><path d="M2 20c1-4 3-6 6-6s5 2 6 6M12 14c1-.5 2-.5 4 0 3 0 5 2 6 6"/></svg></div>

<!-- appointment -->
<section class="abs appt" role="img" aria-label="Dimmed laboratory interior with workbenches"></section>
<h3 class="abs hours-title" style="font-weight:400">Opening Hours</h3>
<div class="abs hours-table">
  <div class="hours-row" style="top:30px"><b>Monday - Thursday</b><span>08am - 05pm</span></div>
  <div class="hours-row" style="top:80px"><b>Saturday</b><span>08am - 02pm</span></div>
  <div class="hours-row" style="top:130px"><b>Phone</b><span>+123 456 7890</span></div>
  <div class="hours-row" style="top:181px"><b>Email</b><span>info@company.com</span></div>
</div>
<div class="abs appt-panel"></div>
<div class="abs" style="left:666px;top:2881px;width:54px;height:54px;border-radius:50%;background:var(--navy);display:flex;align-items:center;justify-content:center"><svg width="24" height="24" viewBox="0 0 24 24" fill="none" stroke="#fff" stroke-width="1.5"><rect x="3" y="5" width="18" height="14" rx="2"/><path d="M3 7l9 6 9-6"/></svg></div>
<div class="abs" style="left:734px;top:2880px;font-size:13px;color:#555">Get in touch with us any day any time</div>
<div class="abs serif" style="left:734px;top:2901px;font-size:33px;color:var(--navy)">Make Appointment</div>
<div class="field" style="left:667px;top:2978px;width:182px">First Name</div>
<div class="field" style="left:867px;top:2978px;width:184px">Last Name</div>
<div class="field" style="left:667px;top:3049px;width:182px">Email Address</div>
<div class="field" style="left:867px;top:3049px;width:184px">Phone Number</div>
<div class="field" style="left:667px;top:3122px;width:384px">Select Subject</div>
<div class="field" style="left:667px;top:3194px;width:384px">dd/mm/yyyy</div>
<a class="abs btn-orange" style="left:667px;top:3268px;width:384px;height:52px;display:flex;align-items:center;justify-content:center;font-size:18px;font-weight:600">SUBMIT</a>

<!-- reviews -->
<section class="abs" style="left:0;top:3378px;width:1200px;height:620px;background:var(--lav)"></section>
<h2 class="abs section-title" style="left:0;top:3456px;font-weight:400">Clients Review</h2>
<p class="abs section-sub" style="left:0;top:3522px">Lorem ipsum dolor sit amet, consectetur adipiscing elit, sed do eiusmod temp<br>or incididunt ut labore et dolore</p>

<article class="abs review" style="left:101px">
  <div class="avatar" role="img" aria-label="Client portrait"></div><div class="qmark">”</div>
  <div class="stars">★★★★★</div>
  <p>Lorem ipsum dolor sit amet, consectetur adipiscing elit, sed do eiusmod or incididun t ut labore et dolore Lorem ipsum dolor sit adipiscing elit, sed do ehjhj</p>
  <h5>Mara Lindqvist</h5><small>BUSINESSMAN</small>
</article>
<article class="abs review" style="left:444px;border-bottom:3px solid var(--orange)">
  <div class="avatar" role="img" aria-label="Client portrait" style="background:linear-gradient(#e4d3b4,#9d8a6d)"></div><div class="qmark" style="color:#1a6fd0">”</div>
  <div class="stars">★★★★★</div>
  <p>Lorem ipsum dolor sit amet, consectetur adipiscing elit, sed do eiusmod or incididun t ut labore et dolore Lorem ipsum dolor sit adipiscing elit, sed do ehjhj</p>
  <h5>Mara Lindqvist</h5><small>BUSINESSMAN</small>
</article>
<article class="abs review" style="left:786px">
  <div class="avatar" role="img" aria-label="Client portrait" style="background:linear-gradient(#9ea6b2,#4d5663)"></div><div class="qmark">”</div>
  <div class="stars">★★★★★</div>
  <p>Lorem ipsum dolor sit amet, consectetur adipiscing elit, sed do eiusmod or incididun t ut labore et dolore Lorem ipsum dolor sit adipiscing elit, sed do ehjhj</p>
  <h5>Mara Lindqvist</h5><small>BUSINESSMAN</small>
</article>

<!-- footer -->
<footer class="abs site-footer"></footer>
<svg class="abs" style="left:0;top:3980px" width="1200" height="130" viewBox="0 0 1200 130">
  <path d="M0 0 H1200 V4 Q600 110 0 4 Z" fill="var(--lav)"/>
  <path d="M240 62 Q600 112 960 62" fill="none" stroke="var(--orange)" stroke-width="3"/>
  <circle cx="602" cy="93" r="27" fill="#fff"/>
  <circle cx="602" cy="93" r="7" fill="var(--orange)"/>
</svg>
<div class="abs" style="left:0;top:4192px;width:1200px;display:flex;justify-content:center">
  <div class="brand" style="color:#fff;font-size:30px"><span class="dot" style="width:20px;height:20px"></span>Wellpath Ledgers</div>
</div>
<nav class="foot-nav">
  <a style="left:334px">HOME</a>
  <a style="left:428px">SERVICES</a>
  <a style="left:534px">ABOUT US</a>
  <a style="left:652px">TESTIMONIALS</a>
  <a style="left:803px">BLOG</a>
</nav>
<div class="abs" style="left:140px;top:4335px;width:920px;height:1px;background:rgba(255,255,255,.35)"></div>
<div class="foot-contact" style="left:178px">
  <div class="ring"><svg width="26" height="26" viewBox="0 0 24 24" fill="none" stroke="#fff" stroke-width="1.4"><circle cx="12" cy="12" r="9"/><path d="M3 12h18M12 3c3 3 3 15 0 18M12 3c-3 3-3 15 0 18"/></svg></div>
  <div style="font-size:11px">123, Building Name, Street<br>City, State XY 123456</div>
</div>
<div class="abs" style="left:430px;top:4376px;width:1px;height:60px;background:rgba(255,255,255,.35)"></div>
<div class="foot-contact" style="left:510px">
  <div class="ring"><svg width="22" height="26" viewBox="0 0 24 24" fill="none" stroke="#fff" stroke-width="1.4"><rect x="6" y="2" width="12" height="20" rx="2"/><path d="M10 18h4"/></svg></div>
  <div>PHONE<br><span style="font-size:11px">(123) 456 7890</span></div>
</div>
<div class="abs" style="left:749px;top:4376px;width:1px;height:60px;background:rgba(255,255,255,.35)"></div>
<div class="foot-contact" style="left:832px">
  <div class="ring"><svg width="24" height="24" viewBox="0 0 24 24" fill="none" stroke="#fff" stroke-width="1.4"><rect x="3" y="5" width="18" height="14" rx="2"/><path d="M3 7l9 6 9-6"/></svg></div>
  <div>EMAIL<br><span style="font-size:11px">info@company.com</span></div>
</div>
<div class="abs bottom-bar"></div>
<div class="abs" style="left:147px;top:4486px;color:#fff;font-size:11px;font-weight:600">WellPath Ledgers</div>
<div class="abs social" style="left:933px"></div>
<div class="abs social" style="left:966px"></div>
<div class="abs social" style="left:999px"></div>
<div class="abs social" style="left:1032px"></div>

</body>
</html>
```